Veldmark Supplies Business Card

Professional business card that stand out to our potential customers. Front and back with clean modern design

Industry/Entity Type

Oil and gas

Contact Information for Business Card

Name, address, website , office phone and cell number

Requirements
Must have
• Editable files for each employee

```html
<!DOCTYPE html>
<html lang="en">
<head>
<meta charset="utf-8">
<title>Veldmark Supplies Business Card</title>
<link href="https://fonts.googleapis.com/css2?family=Montserrat:wght@400;500;700;800&display=swap" rel="stylesheet">
<style>
  :root {
    --brand-blue: #04afd3;
    --brand-red: #f40000;
    --paper: #ffffff;
    --backdrop: #e3e5e5;
  }
  * { box-sizing: border-box; margin: 0; padding: 0; }
  html, body { width: 1200px; height: 900px; overflow: hidden; }
  body {
    background: var(--backdrop);
    font-family: "Montserrat", sans-serif;
    position: relative;
  }
  .card {
    position: absolute;
    top: 40px;
    width: 467px;
    height: 814px;
    border-radius: 60px;
    overflow: hidden;
  }
  /* Back side */
  .card-back { left: 133px; background: var(--brand-blue); }
  .back-mark {
    position: absolute;
    left: 120px; top: 350px;
    width: 110px; height: 110px;
    background: var(--brand-red);
  }
  .back-name {
    position: absolute;
    left: 360px; top: 161px;
    width: 56px; height: 491px;
    writing-mode: vertical-rl;
    transform: rotate(180deg);
    display: flex; align-items: center; justify-content: center;
    font-weight: 800;
    font-size: 38px;
    letter-spacing: 1px;
    color: var(--brand-red);
    white-space: nowrap;
  }
  /* Front side */
  .card-front {
    left: 615px;
    background: linear-gradient(to bottom, var(--paper) 0 260px, var(--brand-blue) 260px 100%);
    color: var(--paper);
    text-align: center;
  }
  .front-wordmark {
    position: absolute;
    left: 34px; right: 34px; top: 30px;
    font-weight: 800;
    font-size: 29px;
    letter-spacing: 1px;
    color: var(--brand-red);
    line-height: 42px;
  }
  .front-mark {
    position: absolute;
    left: 178px; top: 170px;
    width: 110px; height: 110px;
    background: var(--brand-red);
  }
  .front-mark-name {
    position: absolute;
    left: 0; right: 0; top: 300px;
    font-weight: 800;
    font-size: 22px;
    letter-spacing: 2px;
    color: var(--paper);
  }
  .person-name {
    position: absolute;
    left: 0; right: 0; top: 436px;
    font-weight: 700;
    font-size: 32px;
    letter-spacing: 0.5px;
  }
  .person-title {
    position: absolute;
    left: 88px; right: 88px; top: 476px;
    display: flex; align-items: center; gap: 12px;
    font-size: 20px; font-weight: 500;
  }
  .person-title::before, .person-title::after {
    content: ""; flex: 1; height: 2px; background: var(--paper);
  }
  .contact-icons {
    position: absolute;
    left: 0; right: 0; top: 527px;
    display: flex; justify-content: center; gap: 21px;
  }
  .contact-icon {
    width: 36px; height: 36px;
    background: var(--brand-red);
    display: flex; align-items: center; justify-content: center;
  }
  .contact-lines {
    position: absolute;
    left: 0; right: 0; top: 583px;
    font-size: 19px; font-weight: 500;
    line-height: 29px;
  }
  .contact-divider {
    position: absolute;
    left: 118px; right: 118px; top: 718px;
    height: 1px; background: var(--paper);
  }
  .address {
    position: absolute;
    left: 0; right: 0; top: 728px;
    font-size: 20px; font-weight: 500;
    line-height: 29px;
  }
</style>
</head>
<body>
  <section class="card card-back">
    <div class="back-mark"></div>
    <div class="back-name">VELDMARK SUPPLIES</div>
  </section>

  <section class="card card-front">
    <div class="front-wordmark">VELDMARK SUPPLIES</div>
    <div class="front-mark"></div>
    <div class="front-mark-name">VELDMARK SUPPLIES</div>

    <h1 class="person-name">DORIAN HALVEK</h1>
    <p class="person-title">President</p>

    <div class="contact-icons">
      <span class="contact-icon" aria-label="Office phone">
        <svg width="24" height="20" viewBox="0 0 24 20"><path d="M2 7c0-4 20-4 20 0v2h-5V7H7v2H2z" fill="#fff"/><rect x="5" y="10" width="14" height="8" rx="2" fill="#fff"/></svg>
      </span>
      <span class="contact-icon" aria-label="Cell phone">
        <svg width="14" height="24" viewBox="0 0 14 24"><rect x="1" y="1" width="12" height="22" rx="2" fill="none" stroke="#fff" stroke-width="2"/><circle cx="7" cy="19" r="1.5" fill="#fff"/></svg>
      </span>
      <span class="contact-icon" aria-label="Email">
        <svg width="26" height="18" viewBox="0 0 26 18"><rect x="1" y="1" width="24" height="16" fill="none" stroke="#fff" stroke-width="2"/><path d="M1 1l12 9 12-9" fill="none" stroke="#fff" stroke-width="2"/></svg>
      </span>
      <span class="contact-icon" aria-label="Website">
        <svg width="24" height="24" viewBox="0 0 24 24"><circle cx="12" cy="12" r="10" fill="none" stroke="#fff" stroke-width="2"/><ellipse cx="12" cy="12" rx="4" ry="10" fill="none" stroke="#fff" stroke-width="1.5"/><path d="M2 12h20" stroke="#fff" stroke-width="1.5"/></svg>
      </span>
    </div>

    <div class="contact-lines">
      <p>914-555-0187</p>
      <p>914-555-0263</p>
      <p>info@veldmark-supplies.com</p>
      <p>www.veldmark-supplies.com</p>
    </div>
    <div class="contact-divider"></div>
    <div class="address">
      <p>2740 Larkspur Ave, Ste</p>
      <p>100, Brenton, TX 75390</p>
    </div>
  </section>
</body>
</html>
```